Velk Partners Building Business Cards

We need a business card that reflects our business as "Solar Experts" in San Diego. Browse our website www.velkpartners.example our License needs to be displayed as "CSLB# 3867140" our phone number is (619) 555-0187

Save thousands on your electric bills and increase the value of your home while helping to protect the environment. Our solar installation experts will help you design the system that's right for you, using only the highest quality equipment that will look great and give you ideal performance. Our goal is to make you energy independent, and get your electric bill to 0.

Paul Osterby
(619) 555-0187
paul@velkpartners.example

Target Market(s)

Home owners in san diego looking for solar

Industry/Entity Type

Solar Energy

Contact Information for Business Card

Paul Osterby
(619) 555-0187
paul@velkpartners.example

Font styles to use
Other font styles liked:
• Use our logo font

Requirements
Must have
• License needs to be displayed as "CSLB# 3867140" our phone number is (619) 555-0187
Nice to have
• Real images of rooftop home solar in san diego
Should not have
• our business address

```html
<!DOCTYPE html>
<html lang="en">
<head>
<meta charset="utf-8">
<title>Velk Partners Building – Business Card</title>
<link rel="stylesheet" href="https://fonts.googleapis.com/css2?family=Source+Sans+3:ital,wght@0,400;0,600;0,700;1,400&display=swap">
<style>
  :root {
    --navy: #173d78;
    --navy-deep: #1a3f7a;
    --sun: #f8b000;
    --paper: #ffffff;
    --backdrop: #4d4d4d;
  }
  * { box-sizing: border-box; margin: 0; padding: 0; }
  html, body {
    width: 1105px; height: 1200px; overflow: hidden;
    background: var(--backdrop);
    font-family: "Source Sans 3", sans-serif;
  }
  .card {
    position: absolute; left: 193px; width: 718px; height: 410px;
    border-radius: 20px; overflow: hidden;
  }
  .card--front { top: 167px; background: var(--paper); }
  .card--back { top: 623px; background: var(--sun); }

  .front-waves { position: absolute; inset: 0; width: 718px; height: 410px; }

  .brand-name {
    position: absolute; left: 45px; top: 50px;
    font-size: 38px; font-weight: 700; color: var(--navy);
    letter-spacing: -0.3px; line-height: 1;
  }

  .holder { position: absolute; left: 36px; top: 324px; }
  .holder__name { font-size: 28px; font-weight: 600; color: var(--paper); line-height: 1.1; }
  .holder__title { font-size: 21px; font-weight: 400; color: var(--sun); line-height: 1.2; }

  .contact {
    position: absolute; right: 34px; top: 270px;
    list-style: none; text-align: right;
    color: var(--paper); font-size: 19px; line-height: 1;
  }
  .contact li { display: flex; align-items: center; justify-content: flex-end; height: 28px; }
  .contact li.contact__license { margin-right: 0; height: 34px; }
  .contact svg { width: 17px; height: 17px; margin-left: 8px; flex: none; }

  .back-name {
    position: absolute; left: 0; right: 0; top: 150px;
    text-align: center; font-size: 44px; font-weight: 700; color: var(--paper);
  }
  .back-url {
    position: absolute; left: 0; right: 0; top: 338px;
    text-align: center; font-size: 20px; font-style: italic;
    letter-spacing: 4.5px; color: var(--paper);
  }
</style>
</head>
<body>

<section class="card card--front" aria-label="Business card front">
  <svg class="front-waves" viewBox="0 0 718 410" aria-hidden="true">
    <path fill="var(--navy-deep)" d="M0,240 C130,305 260,318 410,268 C530,228 610,222 718,288 L718,410 L0,410 Z"/>
    <path fill="none" stroke="var(--navy-deep)" stroke-width="6" d="M0,228 C140,298 280,298 420,244 C545,196 625,205 718,276"/>
    <path fill="var(--sun)" d="M0,200 C150,272 300,252 450,190 C545,150 615,158 690,222 C605,180 545,186 450,222 C300,282 140,282 0,222 Z"/>
  </svg>

  <div class="brand-name">Velk Partners Building</div>

  <div class="holder">
    <p class="holder__name">Paul Osterby</p>
    <p class="holder__title">CEO/Founder</p>
  </div>

  <ul class="contact">
    <li class="contact__license">CSLB# 3867140</li>
    <li>(619) 555-0187
      <svg viewBox="0 0 16 16" aria-hidden="true"><path fill="var(--sun)" d="M3.5 1.5l2.5 0 1 3.5-1.7 1.2c.8 1.8 2.2 3.2 4 4l1.2-1.7 3.5 1v2.5c0 .8-.7 1.5-1.5 1.5C6.8 13.5 2.5 9.2 2 3c0-.8.7-1.5 1.5-1.5z"/></svg>
    </li>
    <li>paul@velkpartners.example
      <svg viewBox="0 0 16 16" aria-hidden="true"><rect x="1" y="3.5" width="14" height="9.5" rx="1" fill="var(--sun)"/><path d="M1.5 4l6.5 5 6.5-5" fill="none" stroke="var(--navy-deep)" stroke-width="1.3"/></svg>
    </li>
    <li>www.velkpartners.example
      <svg viewBox="0 0 16 16" aria-hidden="true"><circle cx="8" cy="8" r="7" fill="var(--sun)"/><path d="M4 5.5c1.5-.5 2.5.5 2 2s1 2 .5 3.5M10 3.5c-.5 1.5.5 2 1.5 2M9.5 12c.5-1.5 2-1.5 3-1" fill="none" stroke="var(--navy-deep)" stroke-width="1.2"/></svg>
    </li>
  </ul>
</section>

<section class="card card--back" aria-label="Business card back">
  <div class="back-name">Velk Partners Building</div>
  <p class="back-url">www.velkpartners.example</p>
</section>

</body>
</html>
```